Business card design for Automotive workshop

We need a business card for a new automotive repair and tyre shop called Keelstone Prime Automotive located in New Zealand. We are a clean, modern and fresh workshop and company.

Front needs to feature logo,
my name:
Marlo Fenwicke (director)

Address:
48 Tarn Lane
Whitianga 3510

Phone: 07 594 2713
Mobile: 027 451 9362
Email: office@keelstoneautomotive.example.nz
Website: keelstoneautomotive.example.nz

Back needs to feature an area to write down appointment details, date and time.

Also feature a list of jobs and work we do such as,
Vehicle Servicing
All Mechanical Repairs
Warrant of Fitness
Tyres & Wheel Alignments
Automotive Diagnostics
Automotive Parts & Supplies

```html
<!DOCTYPE html>
<html lang="en">
<head>
<meta charset="utf-8">
<title>Keelstone Prime Automotive – Business Card</title>
<link rel="stylesheet" href="https://fonts.googleapis.com/css2?family=Lato:wght@400;700;900&family=Arimo:wght@400&display=swap">
<style>
  :root {
    --brand-red: #e31e24;
    --ink: #1a1a1a;
    --paper: #ffffff;
    --backdrop: #e9e7e4;
  }
  * { box-sizing: border-box; margin: 0; padding: 0; }
  html, body { width: 1200px; height: 1200px; overflow: hidden; }
  body {
    background: var(--backdrop);
    font-family: "Lato", sans-serif;
    color: var(--ink);
    position: relative;
  }
  .card {
    position: absolute;
    left: 187px;
    width: 826px;
    height: 475px;
    background: var(--paper);
    box-shadow: 0 6px 18px rgba(0,0,0,0.18);
    overflow: hidden;
  }
  .card--front { top: 83px; }
  .card--back { top: 643px; }

  .wordmark {
    position: absolute;
    color: var(--brand-red);
    font-weight: 900;
    text-transform: uppercase;
    line-height: 1.05;
    letter-spacing: 0.5px;
  }
  .card--front .wordmark { left: 50px; top: 206px; font-size: 29px; }
  .card--back .wordmark { left: 60px; top: 92px; font-size: 35px; }

  .divider {
    position: absolute;
    left: 400px; top: 130px;
    width: 2px; height: 216px;
    background: var(--brand-red);
  }
  .person { position: absolute; left: 442px; top: 125px; }
  .person__name { color: var(--brand-red); font-weight: 700; font-size: 29px; line-height: 1.2; }
  .person__role { font-size: 19px; margin-top: 2px; }

  .contact-list { position: absolute; left: 446px; top: 208px; right: 24px; list-style: none; }
  .contact-list li {
    display: flex; align-items: center;
    height: 30px;
    font-size: 17px;
    white-space: nowrap;
  }
  .contact-list svg { width: 19px; height: 19px; margin-right: 10px; flex: none; }

  .services {
    position: absolute; left: 512px; top: 36px;
    list-style: none;
    font-family: "Arimo", sans-serif;
    font-size: 19px;
  }
  .services li { height: 28px; display: flex; align-items: center; }
  .services li::before {
    content: ""; width: 7px; height: 7px; border-radius: 50%;
    background: var(--brand-red); margin-right: 9px;
  }

  .appointment { position: absolute; left: 60px; top: 222px; width: 706px; }
  .appointment__title { color: var(--brand-red); font-weight: 700; font-size: 26px; }
  .form-row { display: flex; align-items: flex-end; font-size: 21px; }
  .form-row--name { margin-top: 34px; }
  .form-row--time { margin-top: 18px; }
  .fill-line {
    flex: 1; border-bottom: 2px dotted var(--ink);
    margin: 0 4px 5px 6px; height: 1px;
  }
  .fill-line--short { flex: none; width: 200px; }
  .check { display: inline-flex; align-items: center; margin-left: 6px; }
  .check::before {
    content: ""; width: 15px; height: 15px; border: 2px solid var(--ink);
    margin-right: 5px;
  }
  .date-label { margin-left: 16px; }
  .days {
    display: flex; justify-content: space-between;
    margin-top: 24px; font-size: 21px;
  }
  .days .check { margin-left: 0; }
  .days .check::before { margin-right: 7px; }

  .notice-band {
    position: absolute; left: 0; bottom: 0;
    width: 100%; height: 51px;
    background: var(--brand-red);
    color: var(--paper);
    font-size: 20px;
    display: flex; align-items: center;
    padding-left: 58px;
  }
</style>
</head>
<body>

<section class="card card--front" aria-label="Front of business card">
  <div class="wordmark">Keelstone Prime<br>Automotive</div>
  <div class="divider"></div>
  <div class="person">
    <div class="person__name">Marlo Fenwicke</div>
    <div class="person__role">Director</div>
  </div>
  <ul class="contact-list">
    <li>
      <svg viewBox="0 0 20 20" fill="none" stroke="#e31e24" stroke-width="1.8"><path d="M10 19s-6-6.2-6-10.5a6 6 0 0 1 12 0C16 12.8 10 19 10 19z"/><circle cx="10" cy="8.5" r="2.3"/></svg>
      48 Tarn Lane, Whitianga 3510
    </li>
    <li>
      <svg viewBox="0 0 20 20" fill="#e31e24"><path d="M4.5 2.5l3 .3 1.3 3.6-1.9 1.5a10 10 0 0 0 5.2 5.2l1.5-1.9 3.6 1.3.3 3c0 .9-.8 1.5-1.7 1.5C8.5 17 3 11.5 3 4.2c0-.9.6-1.7 1.5-1.7z"/></svg>
      07 594 2713
    </li>
    <li>
      <svg viewBox="0 0 20 20" fill="none" stroke="#e31e24" stroke-width="1.8"><rect x="5" y="1.5" width="10" height="17" rx="1.5"/><line x1="9" y1="15.5" x2="11" y2="15.5"/></svg>
      027 451 9362
    </li>
    <li>
      <svg viewBox="0 0 20 20" fill="#e31e24"><path d="M1.5 4.5h17v11h-17z"/><path d="M1.5 4.5L10 11l8.5-6.5M1.5 15.5l6-5M18.5 15.5l-6-5" stroke="#fff" stroke-width="1.4" fill="none"/></svg>
      office@keelstoneautomotive.example.nz
    </li>
    <li>
      <svg viewBox="0 0 20 20" fill="none" stroke="#e31e24" stroke-width="1.4"><circle cx="10" cy="10" r="8"/><ellipse cx="10" cy="10" rx="3.5" ry="8"/><line x1="2" y1="10" x2="18" y2="10"/><line x1="3.2" y1="6" x2="16.8" y2="6"/><line x1="3.2" y1="14" x2="16.8" y2="14"/></svg>
      keelstoneautomotive.example.nz
    </li>
  </ul>
</section>

<section class="card card--back" aria-label="Back of business card">
  <div class="wordmark">Keelstone Prime<br>Automotive</div>
  <ul class="services">
    <li>Vehicle Servicing</li>
    <li>All Mechanical Repairs</li>
    <li>Warrant of Fitness</li>
    <li>Tyres &amp; Wheel Alignments</li>
    <li>Automotive Diagnostics</li>
    <li>Automotive Parts &amp; Supplies</li>
  </ul>
  <div class="appointment">
    <h2 class="appointment__title">APPOINTMENT</h2>
    <div class="form-row form-row--name">Name:<span class="fill-line"></span></div>
    <div class="form-row form-row--time">
      Time:<span class="fill-line fill-line--short"></span>
      <span class="check">AM</span><span class="check">PM</span>
      <span class="date-label">Date:</span><span class="fill-line"></span>
    </div>
    <div class="days">
      <span class="check">MON</span>
      <span class="check">TUES</span>
      <span class="check">WED</span>
      <span class="check">THUR</span>
      <span class="check">FRI</span>
      <span class="check">SAT</span>
    </div>
  </div>
  <div class="notice-band">If you are unable to keep your appointment, please call us within 24 hours.</div>
</section>

</body>
</html>
```